Website Design for Harbor Guidance

I am looking to create a website to help military members who are currently serving or have served to have a mentor. The military does an awful job and providing or offering a mentor program. People need someone they can come to with career advice with promotions, networking, building resumes, and pinging ideas off of on the occasion. I want a place where active and separated military members can come to, sign up and pick a program of offerings that make sense. They would register annually, pay for a membership package (can choose up to three) and then get support they need. Annual registration fees would be as follows and they would need to send payment through Paypal or other electronic means (credit card, eft, paypal, echeck, whatever).

I envision some type of registration that centers around the packages offered - this will be where the revision comes in once the framework is completed.

I am looking for very creative designs, and content, given the above, with verbiage around mentorship program. Please be creative for the design, and also put together three packages and price points for them three packages - put together what it would include in each package. We can modify as necessary during revisions. Final design should communicate military members in uniform with corporate leaders, something warm and inviting are important. I also want the abiity to really get this adversited and in the market for people to stumble across it easily.

I have purchased the domain already - harborguidance.com

Target Market(s)

Military, Veterans

Number of Pages Required

1 page

Requirements
Must have
• Military member with corporate look
• Modern and wide
• Warm and inviting
• Registration with ability to collect through PayPal, eCheck, Credit Card, etc)
• Creative design and content for the website based on what is described in the description
• About Section which has information about leadership team
• Contact Us
• Register
• 3 creative packages of what would be included (design this and the content keeping in mind the description)
• Content and the framework
• Some type of packages to consider (just examples but also needs mentoring options:
• https://www.careerdraftsmithy.com/
• https://www.cvbeacon.com/
• We are not going to ba resume writing service but we will offer it as part of our solution - I really want it to be focused around mentorship for job development, professional advice, interacting with peers, managers, leaders (using military acronyms like Supervisors and Leaders NCO's, Officers, etc)
• Blog so we can post topics and interact and respond to questions people have etc

```html
<!DOCTYPE html>
<html lang="en">
<head>
<meta charset="utf-8">
<title>Harbor Guidance</title>
<link href="https://fonts.googleapis.com/css2?family=Lato:wght@400;700;900&display=swap" rel="stylesheet">
<style>
:root{
  --orange:#f26522;
  --blue:#1c6fb8;
  --blue-deep:#1a63a8;
  --ink:#222;
  --text:#444;
  --grey-bg:#f1f1f1;
  --btn-grey:#6d6d6d;
  --footer:#232323;
  --footer-bottom:#1b1b1b;
  --footer-text:#bdbdbd;
}
*{margin:0;padding:0;box-sizing:border-box}
html,body{width:1200px;height:3309px;overflow:hidden}
body{font-family:"Lato",sans-serif;color:var(--text);background:#fff;position:relative}
a{text-decoration:none;color:inherit}
.abs{position:absolute}
.btn{position:absolute;display:flex;align-items:center;justify-content:center;color:#fff;font-weight:700;text-transform:uppercase;font-size:15px;letter-spacing:.3px}
.btn-orange{background:var(--orange)}
.btn-blue{background:var(--blue)}
.btn-grey{background:var(--btn-grey)}
.section-title{position:absolute;left:0;width:1200px;text-align:center;font-size:25px;font-weight:700;color:var(--ink);text-transform:uppercase;letter-spacing:.3px}
.lead{position:absolute;left:75px;width:1050px;text-align:center;font-size:14.5px;line-height:24px;color:var(--text)}

/* header */
.site-header{position:absolute;left:0;top:0;width:1200px;height:100px;background:#fff}
.logo{left:75px;top:30px;font-size:31px;font-weight:900;color:var(--blue);letter-spacing:-.3px;text-transform:uppercase}
.top-phone{left:688px;top:24px;font-size:13px;font-weight:700;color:var(--ink);display:flex;align-items:center;gap:8px}
.main-nav{right:75px;top:66px;display:flex;gap:40px;font-size:13px;font-weight:700;color:var(--ink);text-transform:uppercase}
.main-nav .active{color:var(--blue)}

/* hero */
.hero{position:absolute;left:0;top:100px;width:1200px;height:562px;background:linear-gradient(120deg,#5a5148 0%,#2e2a28 35%,#1d4a7a 60%,#3a3532 85%,#24201e 100%)}
.hero-title{top:195px;width:1200px;text-align:center;color:#fff;font-size:60px;font-weight:700}
.hero-sub{top:270px;left:310px;width:580px;text-align:center;color:#fff;font-size:22px;line-height:27px}
.dots{top:528px;left:570px;display:flex;gap:9px}
.dots span{width:9px;height:9px;border-radius:50%;background:#fff}
.dots span:first-child{background:var(--orange)}

/* features */
.feature{position:absolute;width:230px;text-align:center;color:var(--blue);font-weight:700;font-size:14.5px}
.feature svg{display:block;margin:0 auto 14px}

/* about */
.about{position:absolute;left:0;top:1091px;width:1200px;height:387px;background:var(--grey-bg)}
.about-photo{position:absolute;left:0;top:0;width:600px;height:387px;background:linear-gradient(135deg,#6b5a48,#3d4a5a 50%,#8a7a64)}
.about h2{position:absolute;left:637px;top:80px;font-size:25px;font-weight:700;color:var(--ink);text-transform:uppercase}
.about p{position:absolute;left:637px;top:122px;width:488px;font-size:14.5px;line-height:24px}

/* offers */
.offer-card{position:absolute;top:1641px;width:241px;height:267px;border:1px solid #d0d0d0;text-align:center}
.offer-card .ring{width:86px;height:86px;margin:24px auto 16px;border:2px solid var(--orange);border-radius:50%;display:flex;align-items:center;justify-content:center}
.offer-card h3{font-size:14.5px;line-height:22px;color:var(--blue);font-weight:700;text-transform:uppercase;padding:0 20px;height:48px}
.offer-card p{font-size:14.5px;line-height:22px;padding:6px 26px 0}

/* packages */
.packages{position:absolute;left:0;top:1967px;width:1200px;height:527px;background:linear-gradient(180deg,var(--blue-deep),#1f78c6)}
.packages .section-title{color:#fff;top:60px}
.packages .lead{color:#fff;top:98px}
.pkg{position:absolute;top:191px;width:330px;height:277px;background:#fff;text-align:center}
.pkg .avatar{position:absolute;left:113px;top:-52px;width:104px;height:104px;border-radius:50%;background:#fff;border:3px solid var(--blue);display:flex;align-items:center;justify-content:center}
.pkg h3{margin-top:70px;font-size:15px;font-weight:700;color:var(--ink);text-transform:uppercase}
.pkg .price{margin-top:6px;font-size:16px;color:var(--ink)}
.pkg .price b{color:var(--orange);font-size:26px;font-weight:700}
.pkg .price sup{color:var(--orange);font-size:14px;font-weight:700}
.pkg p{margin-top:8px;padding:0 36px;font-size:14.5px;line-height:22px}
.pkg .btn{top:217px;height:36px;font-size:13px}

/* blog */
.post{position:absolute;top:2598px;width:330px}
.post .thumb{height:199px}
.post h3{margin-top:20px;font-size:14.5px;line-height:23px;color:var(--blue);font-weight:700;text-transform:uppercase}
.post p{margin-top:9px;font-size:14.5px;line-height:23px}
.post p span{color:var(--orange)}

/* footer */
.site-footer{position:absolute;left:0;top:2996px;width:1200px;height:257px;background:var(--footer);color:var(--footer-text);font-size:13.5px}
.foot-col{position:absolute;top:46px}
.foot-col h4{color:#fff;font-size:14px;font-weight:700;text-transform:uppercase;margin-bottom:14px}
.foot-col li{list-style:none;line-height:29px}
.foot-col .brand{color:var(--orange);font-weight:700;text-transform:uppercase;font-size:13px}
.foot-col .line{line-height:24px}
.email-field{width:242px;height:42px;background:#fff;color:#777;font-size:13.5px;padding:12px 14px;margin-top:18px}
.socials{display:flex;gap:17px}
.socials span{width:22px;height:22px;border-radius:50%;background:#fff}
.pay{display:flex;gap:10px}
.pay span{width:43px;height:26px;background:#fff;border-radius:3px}
.copyright{position:absolute;left:0;top:3253px;width:1200px;height:56px;background:var(--footer-bottom);color:#9a9a9a;font-size:12px;text-align:center;line-height:56px}
</style>
</head>
<body>

<header class="site-header">
  <div class="abs logo">Harbor Guidance</div>
  <div class="abs top-phone">
    <svg width="13" height="13" viewBox="0 0 24 24"><path fill="#222" d="M6.6 10.8a15 15 0 0 0 6.6 6.6l2.2-2.2c.3-.3.7-.4 1-.2 1.1.4 2.3.6 3.6.6.6 0 1 .4 1 1V20c0 .6-.4 1-1 1A17 17 0 0 1 3 4c0-.6.4-1 1-1h3.5c.6 0 1 .4 1 1 0 1.3.2 2.5.6 3.6.1.3 0 .7-.2 1z"/></svg>
    CALL: 1-800-555-0142
  </div>
  <a class="btn btn-blue" style="left:866px;top:15px;width:124px;height:32px;font-size:12px">Member Log In</a>
  <a class="btn btn-orange" style="left:1003px;top:15px;width:122px;height:32px;font-size:12px">Register</a>
  <nav class="abs main-nav">
    <a class="active">Home</a><a>About Us</a><a>What We Do</a><a>Membership Packages</a><a>Blog</a><a>Contact Us</a>
  </nav>
</header>

<section class="hero" role="img" aria-label="Photo of a uniformed service member mentoring a corporate professional at a laptop">
  <h1 class="abs hero-title">Harbor Guidance</h1>
  <p class="abs hero-sub">Vestibulum ante ipsum primis in faucibus orci luctus et ultrices posuere cubilia..</p>
  <a class="btn btn-orange" style="left:510px;top:345px;width:178px;height:50px">Get Started</a>
  <div class="abs dots"><span></span><span></span><span></span><span></span></div>
</section>

<section class="welcome">
  <h2 class="section-title" style="top:706px">Welcome to Our Website</h2>
  <p class="lead" style="top:750px">Aliquam molestie, mi et imperdiet euismod, dui purus auctor tellus, et interdum lacus lectus et ante. Sed accumsan sollicitudin sapien, sit amet adipiscing turpis gravida ac. In congue, neque ac lobortis volutpat, libero mauris varius mi, vitae suscipit ipsum ligula vitae risus.</p>
  <div class="feature" style="left:81px;top:840px">
    <svg width="56" height="48" viewBox="0 0 56 48" fill="none" stroke="#f26522" stroke-width="2.5"><rect x="3" y="12" width="50" height="33" rx="3"/><path d="M20 12V5h16v7M12 12v33M44 12v33"/></svg>
    Career Advice with Promotions</div>
  <div class="feature" style="left:348px;top:840px">
    <svg width="56" height="48" viewBox="0 0 56 48" fill="none" stroke="#f26522" stroke-width="2.5"><rect x="20" y="3" width="16" height="12"/><rect x="4" y="33" width="16" height="12"/><rect x="36" y="33" width="16" height="12"/><rect x="20" y="33" width="16" height="12"/><path d="M28 15v18M12 33v-8h32v8"/></svg>
    Networking</div>
  <div class="feature" style="left:620px;top:840px">
    <svg width="56" height="48" viewBox="0 0 56 48" fill="none" stroke="#f26522" stroke-width="2.5"><path d="M14 2h20l10 10v34H14z"/><path d="M34 2v10h10M20 22h18M20 29h18M20 36h18"/></svg>
    Building Resumes</div>
  <div class="feature" style="left:890px;top:840px">
    <svg width="56" height="48" viewBox="0 0 56 48" fill="none" stroke="#f26522" stroke-width="2.5"><path d="M28 3a13 13 0 0 0-8 23v7h16v-7a13 13 0 0 0-8-23z"/><path d="M22 38h12M24 43h8"/></svg>
    Pinging Ideas Off</div>
  <a class="btn btn-orange" style="left:510px;top:968px;width:180px;height:50px">Read More</a>
</section>

<section class="about">
  <div class="about-photo" role="img" aria-label="Photo of a uniformed service member shaking hands with a business leader across a desk"></div>
  <h2>About Harbor Guidance</h2>
  <p>Aliquam molestie, mi et imperdiet euismod, dui purus auctor tellus, et interdum lacus lectus et ante. Sed accumsan sollicitudin sapien, sit amet adipiscing turpis gravida ac. In congue, neque ac lobortis volutpat, libero mauris varius mi, vitae suscipit ipsum ligula vitae risus.</p>
  <a class="btn btn-orange" style="left:637px;top:245px;width:179px;height:51px">Read More</a>
</section>

<section class="offers">
  <h2 class="section-title" style="top:1518px">What We Offers</h2>
  <p class="lead" style="top:1564px">Aliquam molestie, mi et imperdiet euismod, dui purus auctor tellus, et interdum lacus lectus et ante. Sed accumsan sollicitudin sapien, sit amet adipiscing turpis gravida ac. In congue, neque ac lobortis volutpat, libero mauris varius mi, vitae suscipit ipsum ligula vitae risus.</p>
  <div class="offer-card" style="left:75px">
    <div class="ring"><svg width="46" height="40" viewBox="0 0 46 40" fill="#333"><circle cx="12" cy="9" r="5"/><circle cx="34" cy="9" r="5"/><rect x="5" y="16" width="14" height="12" rx="3"/><rect x="27" y="16" width="14" height="12" rx="3"/><rect x="2" y="26" width="42" height="4"/><rect x="10" y="30" width="3" height="9"/><rect x="33" y="30" width="3" height="9"/></svg></div>
    <h3>Mentorship for Job Development</h3>
    <p>Aliquam molestie mi et imperdiet euismod, dui purus auctor tellus..</p>
  </div>
  <div class="offer-card" style="left:345px">
    <div class="ring"><svg width="46" height="40" viewBox="0 0 46 40" fill="#333"><circle cx="23" cy="7" r="5"/><rect x="16" y="14" width="14" height="11" rx="3"/><rect x="4" y="24" width="38" height="4"/><rect x="6" y="15" width="8" height="8"/><rect x="32" y="15" width="8" height="8"/><rect x="8" y="28" width="3" height="11"/><rect x="35" y="28" width="3" height="11"/></svg></div>
    <h3>Professional Advice</h3>
    <p>Aliquam molestie mi et imperdiet euismod, dui purus auctor tellus..</p>
  </div>
  <div class="offer-card" style="left:615px">
    <div class="ring"><svg width="50" height="36" viewBox="0 0 50 36" fill="#333"><path d="M2 10l10-6 10 5 6-3 10 2 10 6-4 4-9-4-10 9c-2 2-5 0-3-2l7-7-4-1-13 11z"/><path d="M8 22l6 6c2 2 5 0 3-2zM16 28l3 3c2 2 5 0 3-2z"/></svg></div>
    <h3>Interacting with Peers</h3>
    <p>Aliquam molestie mi et imperdiet euismod, dui purus auctor tellus..</p>
  </div>
  <div class="offer-card" style="left:885px">
    <div class="ring"><svg width="46" height="40" viewBox="0 0 46 40" fill="#333"><circle cx="23" cy="7" r="5"/><path d="M15 14h16v14h-4v11h-8V28h-4z"/><circle cx="9" cy="13" r="4"/><path d="M3 19h12v9h-3v10H6V28H3z"/><circle cx="37" cy="13" r="4"/><path d="M31 19h12v9h-3v10h-6V28h-3z"/></svg></div>
    <h3>Supervisors and Leaders</h3>
    <p>Aliquam molestie mi et imperdiet euismod, dui purus auctor tellus..</p>
  </div>
</section>

<section class="packages">
  <h2 class="section-title">Membership Packages</h2>
  <p class="lead">Aliquam molestie, mi et imperdiet euismod, dui purus auctor tellus, et interdum lacus lectus et ante.</p>
  <div class="pkg" style="left:75px">
    <div class="avatar"><svg width="54" height="60" viewBox="0 0 54 60" fill="#222"><circle cx="27" cy="16" r="13"/><path d="M4 60c0-16 10-26 23-26s23 10 23 26z"/><path fill="#fff" d="M23 34h8l-4 18z"/></svg></div>
    <h3>Professional</h3>
    <div class="price"><sup>$</sup><b>190</b> 2+ years</div>
    <p>Aliquam molestie, mi et imperdiet euismod, dui purus auctor tellus, et interdum lacus lectus et ante.</p>
    <a class="btn btn-orange" style="left:44px;width:116px">Buy Now</a>
    <a class="btn btn-grey" style="left:170px;width:116px">Learn More</a>
  </div>
  <div class="pkg" style="left:435px">
    <div class="avatar"><svg width="58" height="56" viewBox="0 0 58 56" fill="#222"><circle cx="22" cy="15" r="12"/><path d="M2 54c0-15 9-24 20-24s20 9 20 24z"/><rect x="34" y="34" width="22" height="18" rx="2"/><rect x="40" y="30" width="10" height="5" fill="none" stroke="#222" stroke-width="2"/></svg></div>
    <h3>Executive</h3>
    <div class="price"><sup>$</sup><b>230</b> C-level executives, VPs</div>
    <p>Aliquam molestie, mi et imperdiet euismod, dui purus auctor tellus, et interdum lacus lectus et ante.</p>
    <a class="btn btn-orange" style="left:44px;width:116px">Buy Now</a>
    <a class="btn btn-grey" style="left:170px;width:116px">Learn More</a>
  </div>
  <div class="pkg" style="left:795px">
    <div class="avatar"><svg width="54" height="60" viewBox="0 0 54 60" fill="#222"><path d="M11 12c6-8 26-8 32 0l-2 6H13z"/><circle cx="27" cy="22" r="11"/><path d="M4 60c0-16 10-26 23-26s23 10 23 26z"/></svg></div>
    <h3>Military</h3>
    <div class="price"><sup>$</sup><b>230</b> 2+ years</div>
    <p>Aliquam molestie, mi et imperdiet euismod, dui purus auctor tellus, et interdum lacus lectus et ante.</p>
    <a class="btn btn-orange" style="left:44px;width:116px">Buy Now</a>
    <a class="btn btn-grey" style="left:170px;width:116px">Learn More</a>
  </div>
</section>

<section class="blog">
  <h2 class="section-title" style="top:2540px">Blog Posts</h2>
  <article class="post" style="left:75px">
    <div class="thumb" role="img" aria-label="Photo of two professionals in a meeting at an office table" style="background:linear-gradient(135deg,#2f3b4a,#8a8f94 60%,#c9c6c0)"></div>
    <h3>Nam fermentum vestibulum purus id aliquet aliquam..</h3>
    <p>Aliquam molestie mi et imperdiet euismod, dui purus auctor tellus nibh eget tortor vehicula tempus ac sed massa..<span>Read More</span></p>
  </article>
  <article class="post" style="left:435px">
    <div class="thumb" role="img" aria-label="Photo of colleagues smiling around a laptop in a bright office" style="background:linear-gradient(135deg,#d9d6cf,#9aa3ab 50%,#7c8a6e)"></div>
    <h3>Nam fermentum vestibulum purus id aliquet aliquam..</h3>
    <p>Aliquam molestie mi et imperdiet euismod, dui purus auctor tellus nibh eget tortor vehicula tempus ac sed massa..<span>Read More</span></p>
  </article>
  <article class="post" style="left:795px">
    <div class="thumb" role="img" aria-label="Photo of a uniformed service member on the phone at a desk" style="background:linear-gradient(135deg,#6f6558,#a5977f 50%,#4d4a45)"></div>
    <h3>Nam fermentum vestibulum purus id aliquet aliquam..</h3>
    <p>Aliquam molestie mi et imperdiet euismod, dui purus auctor tellus nibh eget tortor vehicula tempus ac sed massa..<span>Read More</span></p>
  </article>
</section>

<footer class="site-footer">
  <div class="foot-col" style="left:75px">
    <h4>Site Map</h4>
    <ul style="margin-top:-6px"><li>Home</li><li>About Us</li><li>What We Do</li><li>Membership Packages</li><li>Blog</li><li>Contact Us</li></ul>
  </div>
  <div class="foot-col" style="left:325px">
    <h4>Contact Us</h4>
    <div class="brand">Harbor Guidance</div>
    <div class="line">2417 Lantern Quay,<br>Norfolk, VA 23510</div>
    <div class="line" style="margin-top:8px;display:flex;gap:18px;align-items:center">
      <svg width="12" height="12" viewBox="0 0 24 24"><path fill="#bdbdbd" d="M6.6 10.8a15 15 0 0 0 6.6 6.6l2.2-2.2c.3-.3.7-.4 1-.2 1.1.4 2.3.6 3.6.6.6 0 1 .4 1 1V20c0 .6-.4 1-1 1A17 17 0 0 1 3 4c0-.6.4-1 1-1h3.5c.6 0 1 .4 1 1 0 1.3.2 2.5.6 3.6.1.3 0 .7-.2 1z"/></svg>1-800-555-0142</div>
    <div class="line" style="margin-top:6px;display:flex;gap:18px;align-items:center">
      <svg width="12" height="10" viewBox="0 0 24 18"><path fill="#bdbdbd" d="M0 0h24v18H0zM2 2l10 8 10-8z"/></svg>hello@harborguidance.com</div>
  </div>
  <div class="foot-col" style="left:595px">
    <h4>Email Subscribe</h4>
    <div class="line" style="width:240px">Consectetuer adipiscing elit, sed diam nonummy nibh euismod..</div>
    <div class="email-field">Enter Email Address</div>
    <a class="btn btn-orange" style="left:166px;top:181px;width:76px;height:36px;font-size:12px">Sign Up</a>
  </div>
  <div class="foot-col" style="left:915px">
    <h4>Follow Us</h4>
    <div class="socials"><span></span><span></span><span></span><span></span><span></span></div>
    <h4 style="margin-top:38px">Payments</h4>
    <div class="pay"><span></span><span></span><span></span><span></span></div>
  </div>
</footer>
<div class="copyright">Copyright © 2018, Harbor Guidance. All Rights Reserved</div>

</body>
</html>
```